you will use Ai to Copy the website Brivanta.com to come up with the basic frame work and it will give you the understanding of how I would like Kelbrava.com to be like. Kelbrava.com is a peer to peer rv rental site very similar to both of the other rv rental sites the difference is that are commission based 20% and above per rental and we will be one flat monthly rate and they keep all the earnings. Below is photo that will help you with the color scheme and the look and feel of the design

1 page

```html
<!DOCTYPE html>
<html lang="en">
<head>
<meta charset="utf-8">
<title>Kelbrava.com – Find your perfect RV rental</title>
<link href="https://fonts.googleapis.com/css2?family=Prata&family=Outfit:wght@300;400;500;600&display=swap" rel="stylesheet">
<style>
:root{
  --navy:#1c2742;
  --navy-deep:#17213a;
  --green:#5a9b2f;
  --green-dark:#4a8526;
  --ink:#1d2233;
  --muted:#5b6070;
  --line:#dfe3e8;
  --band:#edf0f4;
  --white:#ffffff;
}
*{box-sizing:border-box;margin:0;padding:0}
html,body{width:1200px;height:5324px;overflow:hidden}
body{position:relative;background:var(--white);font-family:"Outfit",sans-serif;color:var(--ink)}
.abs{position:absolute}
.serif{font-family:"Prata",serif;font-weight:400}
.img{position:absolute;overflow:hidden}

/* hero */
.hero{left:0;top:0;width:1200px;height:650px;background:linear-gradient(180deg,#27324a 0%,#3b4d52 35%,#5c6f4e 65%,#7c7452 100%)}
.nav{left:87px;top:22px;width:1040px;height:52px;display:flex;align-items:center;color:var(--white)}
.logo{font-family:"Outfit",sans-serif;font-weight:600;font-size:30px;color:var(--white);letter-spacing:-.5px}
.nav-links{position:absolute;left:320px;font-size:13px}
.nav-links span{position:absolute;top:-8px;white-space:nowrap}
.login{position:absolute;left:902px;top:12px;width:83px;height:30px;border-radius:15px;background:var(--green);font-size:12px;display:flex;align-items:center;justify-content:center}
.burger{position:absolute;left:1013px;top:18px;width:20px}
.burger i{display:block;height:2px;background:var(--white);margin-bottom:5px}
.hero-title{left:0;width:1184px;top:168px;text-align:center;font-size:50px;color:var(--white)}
.hero-sub{left:0;width:1184px;top:248px;text-align:center;font-size:15px;color:var(--white)}
.search{left:136px;top:300px;width:917px;height:67px;background:var(--white);border-radius:6px;display:flex;align-items:center}
.field{height:100%;padding:14px 0 0 20px;border-right:1px solid var(--line)}
.field small{display:block;font-size:9px;color:var(--muted)}
.field b{display:block;font-weight:500;font-size:13px;margin-top:3px}
.go{position:absolute;left:854px;top:9px;width:50px;height:50px;border-radius:50%;background:var(--green)}

/* promo */
.promo{top:708px;width:525px;height:368px;border-radius:4px}
.promo-label{left:40px;bottom:22px;font-size:30px;color:var(--white)}
.pill{position:absolute;height:30px;border-radius:15px;background:var(--white);font-size:11px;color:var(--ink);display:flex;align-items:center;justify-content:center}

h2.sec{position:absolute;font-size:36px;color:var(--ink)}

/* categories */
.cats{left:0;top:1266px;width:1200px;height:240px;overflow:hidden}
.cat{position:absolute;top:0;width:320px;height:239px;border-radius:4px;overflow:hidden}
.cat span.name{position:absolute;left:24px;bottom:22px;font-size:23px;color:var(--white);font-family:"Prata",serif}
.cat .pill{right:22px;bottom:20px;width:80px;height:28px;font-size:9px}
.track{left:114px;top:1568px;width:976px;height:2px;background:var(--line)}
.track i{position:absolute;left:0;top:0;width:272px;height:3px;background:var(--green)}

/* featured */
.tabs{left:124px;top:1737px;width:960px;height:46px}
.tab{position:absolute;top:0;height:46px;border:1px solid var(--line);border-radius:23px;font-size:15px;display:flex;align-items:center;justify-content:center;gap:8px}
.tab.on{background:var(--navy);color:var(--white);border-color:var(--navy)}
.card{position:absolute;width:242px;height:300px;border:1px solid var(--line);border-radius:4px;overflow:hidden;background:var(--white)}
.card .ph{height:172px;position:relative}
.fav{position:absolute;right:8px;top:10px;height:18px;padding:0 7px;border-radius:9px;background:var(--white);font-size:10px;display:flex;align-items:center;gap:3px}
.card h3{margin:18px 0 0 27px;font-size:12px;font-weight:500}
.card p{margin:3px 0 0 27px;font-size:10px;color:var(--muted);line-height:1.45}
.card .price{margin:12px 0 0 27px;font-size:13px;font-weight:600}
.btn{position:absolute;border-radius:23px;background:var(--green);color:var(--white);font-size:15px;font-weight:500;display:flex;align-items:center;justify-content:center}

/* destinations */
.band{left:0;top:2577px;width:1200px;height:521px;background:var(--band)}
.dest{top:2728px;width:311px;height:260px;border-radius:4px}
.dest span{position:absolute;left:26px;bottom:22px;font-size:20px;color:var(--white);font-family:"Prata",serif}

/* earnings */
.earn h2{font-size:40px;line-height:1.35;color:var(--ink)}
.earn p{font-size:15px;color:#3c4150;line-height:1.55}
.feat{position:absolute;left:666px;width:340px;height:44px;border-bottom:1px solid var(--line);display:flex;align-items:center;gap:22px;font-size:14px;font-weight:500;letter-spacing:.5px;color:var(--ink)}

/* city list */
.city{position:absolute;font-size:13px;color:var(--ink)}
.city small{display:block;font-size:12px;color:var(--muted);margin:8px 0 0 22px}
.city svg{vertical-align:-3px;margin-right:8px}

/* cta */
.cta-bg{left:0;top:4170px;width:1200px;height:745px;background:linear-gradient(180deg,#ffffff 0%,#ffffff 45%,#c7d6df 58%,#7d9a86 70%,#3d5c3a 85%,#59604f 100%)}
.eyebrow{left:0;width:1200px;top:4350px;text-align:center;font-size:14px;font-weight:600;color:var(--green);letter-spacing:1.5px}

/* footer */
.foot{left:0;top:4915px;width:1200px;height:409px;background:var(--navy-deep);color:var(--white)}
.fcol{position:absolute;top:84px;font-size:11px}
.fcol h4{font-size:12px;font-weight:600;margin-bottom:14px}
.fcol li{list-style:none;color:#c7cdd9;margin-bottom:10px}
.social{position:absolute;top:127px;width:24px;height:24px;border-radius:50%;background:var(--white)}
.legal{left:118px;top:5271px;width:980px;display:flex;justify-content:space-between;font-size:11px;color:#c7cdd9}
</style>
</head>
<body>

<!-- Hero -->
<section class="abs hero" role="img" aria-label="Class C motorhome parked in a green valley with forested mountains behind"></section>
<header class="abs nav">
  <span class="logo">Kelbrava.com</span>
  <nav class="nav-links">
    <span style="left:0">Find an RV</span>
    <span style="left:115px">List Your RV</span>
    <span style="left:239px">How it Works</span>
    <span style="left:371px">Resources</span>
    <span style="left:493px">&#9679; Sign Up</span>
  </nav>
  <span class="login">Log In</span>
  <span class="burger"><i></i><i></i><i></i></span>
</header>
<h1 class="abs serif hero-title">Find your perfect RV rental</h1>
<p class="abs hero-sub">Explore the best travel trailers, motorhomes, and camper vans for your RV adventure.</p>
<form class="abs search">
  <div class="field" style="width:300px;position:relative"><small>Location</small><b>Amsterdam, NH</b><span style="position:absolute;right:14px;top:24px;color:#aaa;font-size:14px">&times;</span></div>
  <div class="field" style="width:168px"><small>Dates</small><b>Any Dates</b></div>
  <div class="field" style="width:130px"><small>Guests</small><b>2 guests</b></div>
  <div class="field" style="width:115px"><small>Driver's age</small><b>25+</b></div>
  <div class="field" style="border:0"><small>Rental Type</small><b>All Type</b></div>
  <span class="go"><svg width="50" height="50" viewBox="0 0 50 50"><circle cx="23" cy="23" r="7" fill="none" stroke="#fff" stroke-width="2"/><path d="M28 28l6 6" stroke="#fff" stroke-width="2"/></svg></span>
</form>

<!-- Promo cards -->
<div class="img promo" style="left:68px;background:linear-gradient(180deg,#8a9468,#5f6e4a 60%,#3c4433)" role="img" aria-label="Pickup truck towing a fifth wheel trailer">
  <span class="abs serif promo-label">Drive it or Tow it</span>
  <span class="pill" style="left:405px;bottom:20px;width:95px">Book Now</span>
</div>
<div class="img promo" style="left:607px;background:linear-gradient(180deg,#4f5f45,#3f4b39 60%,#2d3628)" role="img" aria-label="Travel trailer with awning set up at a shaded campsite">
  <span class="abs serif promo-label" style="left:28px">Delivery &amp; On-Site Stays</span>
  <span class="pill" style="left:399px;bottom:28px;width:103px">Pick it up</span>
</div>

<!-- Find your perfect RV -->
<h2 class="sec serif" style="left:97px;top:1170px">Find Your Perfect RV</h2>
<div class="abs cats">
  <div class="cat" style="left:99px;background:linear-gradient(180deg,#c9d3d8,#93a07c 60%,#6d7552)" role="img" aria-label="Travel trailer parked in a grassy field"><span class="name">Travel Trailers</span><span class="pill">Book now</span></div>
  <div class="cat" style="left:433px;background:linear-gradient(180deg,#9fc0d6,#7c9a70 60%,#5a7048)" role="img" aria-label="Compact camper trailer beside a lake"><span class="name">Camper Trailers</span><span class="pill" style="background:var(--green);color:#fff">Book now</span></div>
  <div class="cat" style="left:767px;background:linear-gradient(180deg,#8aa16e,#6b8157 60%,#4d5e3f)" role="img" aria-label="Fifth wheel trailers lined up on grass"><span class="name">Fifth Wheels</span><span class="pill">Book now</span></div>
  <div class="cat" style="left:1101px;background:linear-gradient(180deg,#7fa3c4,#6c8a6a 60%,#4b5f44)" role="img" aria-label="Fifth wheel trailer beneath mountains"><span class="name">Fifth Wheels</span></div>
</div>
<div class="abs track"><i></i></div>

<!-- Featured -->
<h2 class="sec serif" style="left:111px;top:1638px">Featured RV Rental</h2>
<p class="abs" style="left:609px;top:1643px;width:500px;font-size:15px;color:#3c4150;line-height:1.3">From compact campervans to spacious motorhomes, discover RVs that fit your trip, your crew, and your travel style.</p>
<div class="abs tabs">
  <span class="tab on" style="left:0;width:177px">&#9825; Popular</span>
  <span class="tab" style="left:200px;width:178px"><svg width="22" height="14" viewBox="0 0 22 14"><rect x="1" y="2" width="16" height="8" rx="2" fill="none" stroke="#1d2233" stroke-width="1.4"/><circle cx="6" cy="12" r="1.6" fill="#1d2233"/><circle cx="14" cy="12" r="1.6" fill="#1d2233"/></svg>Camper Van</span>
  <span class="tab" style="left:388px;width:182px">&#9671; Values</span>
  <span class="tab" style="left:582px;width:178px"><svg width="20" height="14" viewBox="0 0 20 14"><rect x="1" y="2" width="15" height="8" rx="3" fill="none" stroke="#1d2233" stroke-width="1.4"/><circle cx="8" cy="12" r="1.6" fill="#1d2233"/></svg>Vintage</span>
  <span class="tab" style="left:762px;width:194px"><svg width="20" height="14" viewBox="0 0 20 14"><rect x="1" y="2" width="14" height="8" rx="2" fill="none" stroke="#1d2233" stroke-width="1.4"/><circle cx="7" cy="12" r="1.6" fill="#1d2233"/></svg>Small Trailers</span>
</div>

<article class="card" style="left:114px;top:1838px"><div class="ph" style="background:linear-gradient(180deg,#c88a4a,#8b6a3c 60%,#6e7a5a)" role="img" aria-label="Class C motorhome on an autumn hillside road"><span class="fav">60 &#9825;</span></div><h3>2024 Wind Jamming Solace</h3><p>Fifth Wheel<br>Lynn Haven FL</p><div class="price">$110 / night</div></article>
<article class="card" style="left:374px;top:1838px"><div class="ph" style="background:linear-gradient(180deg,#b9c7d2,#e6e8ea 55%,#6f7768)" role="img" aria-label="Camper van motorhome parked on pavement"><span class="fav">60 &#9825;</span></div><h3>2024 Wind Jamming Solace</h3><p>Camper Van<br>Lynn Haven FL</p><div class="price">$110 / night</div></article>
<article class="card" style="left:633px;top:1838px"><div class="ph" style="background:linear-gradient(180deg,#c3d2de,#e4e6e8 55%,#87907c)" role="img" aria-label="White travel trailer on a paved lot"><span class="fav">60 &#9825;</span></div><h3>2024 Wind Jamming Solace</h3><p>Travel Trailer<br>Lynn Haven FL</p><div class="price">$110 / night</div></article>
<article class="card" style="left:893px;top:1838px"><div class="ph" style="background:linear-gradient(180deg,#3e5a40,#d9dcd7 55%,#6a7564)" role="img" aria-label="Camper van trailer beside trees"><span class="fav">60 &#9825;</span></div><h3>2024 Wind Jamming Solace</h3><p>Camper Van<br>Lynn Haven FL</p><div class="price">$110 / night</div></article>

<article class="card" style="left:114px;top:2158px"><div class="ph" style="background:linear-gradient(180deg,#9db6c6,#e3e6e8 55%,#7e8d6d)" role="img" aria-label="Fifth wheel trailer by a lake"><span class="fav">60 &#9825;</span></div><h3>2024 Wind Jamming Solace</h3><p>Fifth Wheel<br>Lynn Haven FL</p><div class="price">$110 / night</div></article>
<article class="card" style="left:374px;top:2158px"><div class="ph" style="background:linear-gradient(180deg,#5d7d52,#e5e6e4 55%,#6e7c5e)" role="img" aria-label="Fifth wheel trailer parked on grass"><span class="fav">60 &#9825;</span></div><h3>2024 Wind Jamming Solace</h3><p>Fifth Wheel<br>Lynn Haven FL</p><div class="price">$110 / night</div></article>
<article class="card" style="left:633px;top:2158px"><div class="ph" style="background:linear-gradient(180deg,#a9c3da,#dfe2e4 50%,#6f9a4a)" role="img" aria-label="Vintage trailer on a green meadow"><span class="fav">60 &#9825;</span></div><h3>2024 Wind Jamming Solace</h3><p>v<br>Lynn Haven FL</p><div class="price">$110 / night</div></article>
<article class="card" style="left:893px;top:2158px"><div class="ph" style="background:linear-gradient(180deg,#8b4e40,#d8dadb 55%,#7f8576)" role="img" aria-label="Fifth wheel trailer in front of a brick building"><span class="fav">60 &#9825;</span></div><h3>2024 Wind Jamming Solace</h3><p>Fifth Wheel<br>Lynn Haven FL</p><div class="price">$110 / night</div></article>

<a class="btn" style="left:527px;top:2497px;width:171px;height:45px">View More</a>

<!-- Popular destinations -->
<section class="abs band"></section>
<h2 class="sec serif" style="left:0;width:1184px;text-align:center;top:2638px">Popular Desitnations</h2>
<svg class="abs" style="left:54px;top:2832px" width="24" height="42" viewBox="0 0 24 42"><path d="M20 2L4 21l16 19" fill="none" stroke="#5a9b2f" stroke-width="3"/></svg>
<svg class="abs" style="left:1110px;top:2832px" width="24" height="42" viewBox="0 0 24 42"><path d="M4 2l16 19L4 40" fill="none" stroke="#5a9b2f" stroke-width="3"/></svg>
<div class="img dest" style="left:112px;background:linear-gradient(180deg,#8fa6b8,#6f7b6a 45%,#3f5535 80%,#2e3c2a)" role="img" aria-label="Granite cliffs and river valley at Yosemite"><span>Yosemite, CA</span></div>
<div class="img dest" style="left:444px;background:linear-gradient(180deg,#3d6fb3,#9cb6cf 40%,#5e8b48 75%,#3f6a30)" role="img" aria-label="Mountains above green rolling hills"><span>Hill Country, TX</span></div>
<div class="img dest" style="left:776px;background:linear-gradient(180deg,#7e9bc3,#b06a3a 50%,#a8451f 75%,#3f3a30)" role="img" aria-label="Autumn trees around a lakeside house"><span>Bayfield, CO</span></div>

<!-- Earnings -->
<div class="img" style="left:0;top:3252px;width:287px;height:418px;background:linear-gradient(180deg,#5d7a45,#8ea06a 40%,#d7dbd9 65%,#6c7760)" role="img" aria-label="Class B motorhome parked among pine trees"></div>
<div class="img" style="left:301px;top:3195px;width:294px;height:415px;background:linear-gradient(180deg,#b7b59c,#7f8a66 45%,#556247)" role="img" aria-label="Couple relaxing outside their RV at a campsite"></div>
<span class="abs" style="left:610px;top:3292px;width:30px;height:1px;background:#a3b58a"></span>
<div class="abs earn" style="left:661px;top:3200px;width:460px">
  <h2 class="serif">Your RV.<br>Your Earnings.</h2>
  <p style="margin:20px 0 0 8px">Why give away a large percentage of every rental?</p>
  <p style="margin:12px 0 0 8px">Kelbrava offers RV owners a simpler alternative to commission-based rental marketplaces. Instead of losing 20% or more from each rental, you pay one flat monthly rate and keep your rental earnings.</p>
</div>
<div class="feat" style="top:3488px"><svg width="22" height="22" viewBox="0 0 22 22"><rect x="2" y="3" width="18" height="17" rx="2" fill="#5a9b2f"/><text x="11" y="17" font-size="12" text-anchor="middle" fill="#fff" font-family="Outfit">$</text></svg>ONE FLAT MONTHLY RATE</div>
<div class="feat" style="top:3548px"><svg width="24" height="22" viewBox="0 0 24 22"><circle cx="14" cy="7" r="6" fill="#5a9b2f"/><path d="M1 16h8l4 2h8v3H1z" fill="#5a9b2f"/></svg>KEEP YOUR RENTAL EARNINGS</div>
<div class="feat" style="top:3608px;border:0"><svg width="22" height="22" viewBox="0 0 22 22"><circle cx="11" cy="11" r="9" fill="none" stroke="#5a9b2f" stroke-width="3" stroke-dasharray="4 2.5"/><circle cx="11" cy="11" r="4" fill="#5a9b2f"/></svg>YOU STAY IN CONTROL</div>

<!-- City list -->
<h2 class="sec serif" style="left:117px;top:3817px;font-size:32px">Popular RV Rental Desitnation</h2>
<svg width="0" height="0" style="position:absolute"><defs><symbol id="pin" viewBox="0 0 14 16"><path d="M7 1a5 5 0 0 1 5 5c0 4-5 9-5 9S2 10 2 6a5 5 0 0 1 5-5z" fill="none" stroke="#1d2233" stroke-width="1.2"/><circle cx="7" cy="6" r="1.8" fill="#1d2233"/></symbol></defs></svg>
<div class="city" style="left:108px;top:3913px"><svg width="14" height="16"><use href="#pin"/></svg>Atlanta, GA<small>751 RV rentals</small></div>
<div class="city" style="left:308px;top:3913px"><svg width="14" height="16"><use href="#pin"/></svg>Chicago, IL<small>455 RV rentals</small></div>
<div class="city" style="left:525px;top:3913px"><svg width="14" height="16"><use href="#pin"/></svg>Houston, TX<small>567 RV rentals</small></div>
<div class="city" style="left:737px;top:3913px"><svg width="14" height="16"><use href="#pin"/></svg>Las Vegas, NV<small>436 RV rentals</small></div>
<div class="city" style="left:941px;top:3913px"><svg width="14" height="16"><use href="#pin"/></svg>New York, NY<small>436 RV rentals</small></div>
<div class="city" style="left:108px;top:3993px"><svg width="14" height="16"><use href="#pin"/></svg>Austin, TX<small>783 RV rentals</small></div>
<div class="city" style="left:308px;top:3993px"><svg width="14" height="16"><use href="#pin"/></svg>Columbus, OH<small>410 RV rentals</small></div>
<div class="city" style="left:525px;top:3993px"><svg width="14" height="16"><use href="#pin"/></svg>Kailua-Kona, HI<small>148 RV rentals</small></div>
<div class="city" style="left:737px;top:3993px"><svg width="14" height="16"><use href="#pin"/></svg>Maui, HI<small>149 RV rentals</small></div>
<div class="city" style="left:941px;top:3993px"><svg width="14" height="16"><use href="#pin"/></svg>Oklahoma City, OK<small>149 RV rentals</small></div>
<div class="city" style="left:108px;top:4072px"><svg width="14" height="16"><use href="#pin"/></svg>Boston, MA<small>351 RV rentals</small></div>
<div class="city" style="left:308px;top:4072px"><svg width="14" height="16"><use href="#pin"/></svg>Dallas, TX<small>715 RV rentals</small></div>
<div class="city" style="left:525px;top:4072px"><svg width="14" height="16"><use href="#pin"/></svg>Kauai, HI<small>82 RV rentals</small></div>
<div class="city" style="left:737px;top:4072px"><svg width="14" height="16"><use href="#pin"/></svg>Nashville, TN<small>311 RV rentals</small></div>
<div class="city" style="left:941px;top:4072px"><svg width="14" height="16"><use href="#pin"/></svg>Orlando, FL<small>311 RV rentals</small></div>

<!-- CTA -->
<section class="abs cta-bg" role="img" aria-label="Motorhomes driving a curving mountain highway through pine forest"></section>
<p class="abs eyebrow">START YOUR JOURNEY</p>
<h2 class="sec serif" style="left:0;width:1200px;text-align:center;top:4378px;font-size:40px">Where Will the Road Take You?</h2>
<p class="abs" style="left:240px;width:720px;top:4446px;text-align:center;font-size:15px;color:#3c4150;line-height:1.5">Whether you're looking for an RV for your next adventure or want to put your RV to work when you're not using it, Kelbrava gives you a simple place to get started.</p>
<a class="btn" style="left:418px;top:4518px;width:172px;height:46px">Find an RV &#8599;</a>
<a class="btn" style="left:606px;top:4518px;width:174px;height:46px;background:var(--navy)">List Your RV &#8599;</a>

<!-- Footer -->
<footer class="abs foot">
  <span class="logo abs" style="left:109px;top:78px">Kelbrava.com</span>
  <span class="social" style="left:124px"></span>
  <span class="social" style="left:160px"></span>
  <span class="social" style="left:196px"></span>
  <span class="social" style="left:232px"></span>
  <span class="social" style="left:268px"></span>
  <div class="fcol" style="left:405px"><h4>Navigation</h4><ul><li>Where it all began</li><li>Careers</li><li>Stories and news</li><li>Travel journal</li><li>About</li></ul></div>
  <div class="fcol" style="left:599px"><h4>Guest travel</h4><ul><li>Group bookings</li><li>National park guides</li><li>One-way rentals</li><li>Road trip guides</li><li>RV parks &amp; campgrounds</li><li>Guide to all RV types</li></ul></div>
  <div class="fcol" style="left:816px"><h4>Hosting</h4><ul><li>Become an RV host</li><li>Roadlane demo</li><li>Affiliate program</li><li>RV insurance</li><li>Host iOS app</li><li>Host Android app</li></ul></div>
  <div class="fcol" style="left:1012px"><h4>Support</h4><ul><li>How it works</li><li>Help center</li><li>LLM info</li><li>Contact</li></ul></div>
  <span class="abs" style="left:0;top:340px;width:1200px;height:1px;background:#5a9b2f"></span>
</footer>
<div class="abs legal"><span>&copy; 2026 Kelbrava. All rights reserved.</span><span>Terms &nbsp;|&nbsp; Privacy &nbsp;|&nbsp; Sitemap</span></div>

</body>
</html>
```